Morlavik APP redesign and color change

I am looking for a new design for my app. Please see the attached current design.

Currently, I have a functioning app but the colors and design are awful!
The logo is great but the rest of the app needs a refresh.
(Logo hi res not yet available but will upload soon.)
New colors or anything that is cutting edge.

Basically: It is a secure social media app within a school system where the teachers, students and parents can text, exchange photos, plan curriculum, etc.

I NEED ONLY landing page with a new look!
Looking for one distinct design for the landing page with new look.
The developer will apply this one design towards the rest of the pages/app screens.

Because part of the social media I need the feel and look of what is now the trend. Something that will attract and keep the client(s) interested. I am really leaving all the creative work to the designer and open to any suggestions.

Target Market(s)

Schools, community, teachers, students, colleges, sport teams

Industry/Entity Type

Non Profit

Font styles to use
Serif
Sans Serif

Colors

Designer to choose colors to be used in the design.

Requirements
Must have
• Sharp, trendy, millennial feel
Nice to have
• Up to designer
Should not have
• Up to designer

```html
<!DOCTYPE html>
<html lang="en">
<head>
<meta charset="UTF-8">
<title>Morlavik – Sign In</title>
<link rel="stylesheet" href="https://fonts.googleapis.com/css2?family=Lato:wght@400;700&family=Roboto:wght@400&display=swap">
<style>
  :root {
    --photo-light: #e7b98c;
    --photo-mid: #b9825a;
    --photo-rose: #c9908a;
    --photo-dark: #3a2a2c;
    --veil-top: rgba(238, 214, 120, 0.55);
    --veil-mid: rgba(196, 170, 40, 0.55);
    --veil-bottom: rgba(96, 118, 10, 0.85);
    --white: #ffffff;
    --label: #b37b12;
    --ink: #2b2b2b;
    --rule: #6e6e6e;
    --button: #b77c00;
    --arrow: #111111;
  }
  * { box-sizing: border-box; margin: 0; padding: 0; }
  html, body { width: 741px; height: 1200px; overflow: hidden; }
  body { position: relative; font-family: "Lato", sans-serif; background: var(--photo-mid); }

  .hero-photo {
    position: absolute; inset: 0;
    background:
      radial-gradient(ellipse at 20% 88%, var(--photo-dark) 0%, rgba(58,42,44,0) 45%),
      radial-gradient(ellipse at 70% 20%, var(--photo-light) 0%, rgba(231,185,140,0) 60%),
      linear-gradient(160deg, var(--photo-rose) 0%, var(--photo-mid) 55%, #5b4a2a 100%);
  }
  .brand-veil {
    position: absolute; left: 79px; top: 22px; right: 0; bottom: 0;
    background: linear-gradient(180deg, var(--veil-top) 0%, var(--veil-mid) 50%, var(--veil-bottom) 100%);
  }

  .wordmark {
    position: absolute; left: 240px; top: 517px; width: 322px;
    color: var(--white); font-family: "Lato", sans-serif; font-weight: 700;
    font-size: 31px; letter-spacing: 14px; text-align: center; line-height: 1;
  }

  .login-card {
    position: absolute; left: 132px; top: 653px; width: 556px;
    background: var(--white);
    box-shadow: 0 18px 40px rgba(40, 50, 0, 0.25);
  }
  .login-fields { padding: 62px 62px 50px; height: 317px; }
  .field-label {
    display: block; color: var(--label); font-size: 16px;
    letter-spacing: 2px; text-transform: uppercase; line-height: 1;
  }
  .field-value {
    font-family: "Roboto", sans-serif; color: var(--ink);
    font-size: 23px; line-height: 1;
  }
  .field-username { margin-top: 22px; padding-bottom: 26px; border-bottom: 1.5px solid var(--rule); }
  .field-label-password { margin-top: 38px; }
  .field-password { margin-top: 28px; font-size: 20px; letter-spacing: 3px; }

  .submit-button {
    display: flex; align-items: center; justify-content: space-between;
    height: 106px; padding: 0 62px; background: var(--button);
    color: var(--white); font-size: 23px;
  }

  .signup-prompt {
    position: absolute; left: 132px; width: 556px; top: 1121px;
    text-align: center; color: var(--white); font-size: 18px;
  }
</style>
</head>
<body>
  <div class="hero-photo" role="img" aria-label="Close-up of a person holding a smartphone beside a tan leather bag"></div>
  <div class="brand-veil"></div>

  <div class="wordmark">MORLAVIK</div>

  <form class="login-card">
    <div class="login-fields">
      <span class="field-label">Username</span>
      <div class="field-value field-username">rhea@mailnest.com</div>
      <span class="field-label field-label-password">Password</span>
      <div class="field-value field-password">&#9679;&#9679;&#9679;&#9679;&#9679;&#9679;&#9679;&#9679;</div>
    </div>
    <div class="submit-button">
      <span>Get Started</span>
      <svg width="13" height="18" viewBox="0 0 13 18" aria-hidden="true"><path d="M0 0 L13 9 L0 18 Z" fill="var(--arrow)"/></svg>
    </div>
  </form>

  <p class="signup-prompt">Not registered? Create Account</p>
</body>
</html>
```